Email design required

We need a design for a paid B2B email campaign and facebook / retargeting banner ads that match the same style.

Website: http://pelmora.staging.hostvantry.com/
Campaign Name: KEX Weariness
Example: http://liftmarrowsites.com/kex-weariness/
- I made this over the weekend. It has the right words, but the style / layout needs to change

Size: 600 pixels wide, no limit on length

Formatting:
Format CSS inline only - This will ensure that size, font family, colour, line height, etc. will all remain the same once it is dropped into our newsletter sending software. See below as an

example,

Here's a mockup of

Target Market(s)

Canadian mortgage brokers

Industry/Entity Type

Campaign

Font styles to use
Sans Serif

Colors
3277b5

Requirements
Must have
• Text from my website example http://liftmarrowsites.com/kex-weariness/
• Otherwise, do whatever you think would look good.

```html
<!DOCTYPE html>
<html lang="en">
<head>
<meta charset="utf-8">
<title>Pelmora – KEX Weariness Email</title>
<link href="https://fonts.googleapis.com/css2?family=Open+Sans:ital,wght@0,400;0,600;0,700;1,400&display=swap" rel="stylesheet">
<style>
  :root {
    --page-bg: #2b2b2d;
    --navy: #233354;
    --brand-blue: #3277b5;
    --logo-blue: #1f6cb8;
    --orange: #f7941d;
    --header-bg: #f7f7f7;
    --white: #ffffff;
    --text-grey: #777777;
    --text-dark: #222222;
    --row-light: #383d4a;
    --row-dark: #262626;
    --about-bg: #ececec;
    --footer-bg: #3d3a4d;
  }
  * { box-sizing: border-box; margin: 0; padding: 0; }
  html, body {
    width: 960px; height: 1200px; overflow: hidden;
    background: var(--page-bg);
    font-family: "Open Sans", Arial, sans-serif;
  }
  .email {
    position: absolute; left: 236px; top: 136px;
    width: 600px; height: 1206px;
    transform: scale(0.8); transform-origin: top left;
    background: var(--white);
  }
  .email section, .email header, .email footer { position: relative; }

  .topbar { height: 74px; background: var(--header-bg); }
  .brand-name { position: absolute; left: 27px; top: 18px; font-size: 26px; font-weight: 600; color: var(--logo-blue); letter-spacing: -0.3px; }
  .brand-mark { display: inline-block; width: 18px; height: 18px; background: var(--logo-blue); margin-right: 6px; vertical-align: -1px; }
  .topbar-link { position: absolute; right: 36px; top: 28px; font-size: 14px; color: var(--text-grey); }

  .hero { height: 258px; background: var(--navy); color: var(--white); }
  .hero-title { position: absolute; left: 0; right: 0; top: 4px; text-align: center; font-size: 36px; font-weight: 700; }
  .hero-offer { position: absolute; left: 30px; width: 285px; top: 98px; text-align: center; font-size: 14.5px; line-height: 20px; font-weight: 600; }
  .hero-offer .price { color: var(--orange); }
  .hero-button { position: absolute; left: 72px; top: 162px; width: 180px; height: 43px; border-radius: 22px; background: var(--orange); color: var(--white); font-size: 14.5px; font-weight: 700; text-align: center; line-height: 43px; }
  .hero-art { position: absolute; left: 342px; top: 78px; width: 184px; height: 146px; background: linear-gradient(180deg, #3a4b70, #2c3d60); border-radius: 4px; }

  .band { height: 48px; background: var(--brand-blue); color: var(--white); text-align: center; font-size: 17px; font-weight: 700; line-height: 46px; }

  .review { height: 169px; }
  .avatar { position: absolute; left: 60px; top: 17px; width: 124px; height: 124px; border-radius: 50%; background: #555555; }
  .review-quote { position: absolute; left: 247px; top: 28px; width: 320px; font-size: 13px; line-height: 20px; font-style: italic; color: var(--text-grey); }
  .review-author { position: absolute; left: 247px; top: 116px; font-size: 13.5px; color: var(--text-grey); }

  .compare { height: 222px; }
  .compare-brand { position: absolute; left: 235px; top: 26px; font-size: 21px; font-weight: 600; color: var(--logo-blue); }
  .compare-brand .brand-mark { width: 15px; height: 15px; margin-right: 5px; }
  .compare-rival { position: absolute; left: 440px; top: 30px; font-size: 15px; font-weight: 700; color: var(--text-dark); }
  .compare-table { position: absolute; left: 42px; top: 74px; width: 504px; border-collapse: collapse; color: var(--white); font-size: 13px; }
  .compare-table tr { height: 34px; }
  .compare-table tr:nth-child(odd) { background: var(--row-light); }
  .compare-table tr:nth-child(even) { background: var(--row-dark); }
  .compare-table td { padding: 0; vertical-align: middle; }
  .compare-table .label { width: 160px; padding-left: 5px; }
  .compare-table .label svg { vertical-align: -3px; margin-right: 13px; }
  .compare-table .ours { width: 175px; text-align: center; font-weight: 700; font-size: 13.5px; }
  .compare-table .theirs { text-align: center; }

  .cta-area { height: 99px; border-top: 1px solid #eeeeee; }
  .cta-button { position: absolute; left: 141px; top: 3px; width: 318px; height: 76px; border-radius: 38px; background: var(--orange); color: var(--white); text-align: center; }
  .cta-main { display: block; font-size: 23px; font-weight: 700; padding-top: 10px; line-height: 30px; letter-spacing: 0.5px; }
  .cta-sub { display: block; font-size: 14px; font-weight: 700; letter-spacing: 0.3px; }

  .about { height: 240px; display: flex; }
  .about-visual { position: relative; width: 300px; height: 240px; background: linear-gradient(135deg, #3b5a92, #23406f); }
  .about-visual-name { position: absolute; left: 0; right: 0; top: 118px; text-align: center; font-size: 40px; font-weight: 600; color: var(--white); }
  .about-content { width: 300px; background: var(--about-bg); }
  .about-content .band { height: 47px; font-weight: 400; }
  .about-text { padding: 10px 28px 0 30px; font-size: 13px; line-height: 20px; color: var(--text-grey); }

  .footer { height: 47px; background: var(--footer-bg); color: var(--white); font-size: 13px; }
  .footer-copy { position: absolute; left: 29px; top: 14px; }
  .footer-unsub { position: absolute; right: 32px; top: 14px; }
</style>
</head>
<body>
<main class="email">
  <header class="topbar">
    <div class="brand-name"><span class="brand-mark"></span>Pelmora</div>
    <div class="topbar-link">Contact</div>
  </header>

  <section class="hero">
    <h1 class="hero-title">Experiencing KEX Weariness?</h1>
    <p class="hero-offer">Unlimited Notice of Assessment Orders<br>For Just <span class="price">$29 / Month</span></p>
    <div class="hero-button">Get Started Now</div>
    <div class="hero-art" role="img" aria-label="Illustration of a tired office worker slumped over a desk"></div>
  </section>

  <section class="band">Customer Reviews</section>

  <section class="review">
    <div class="avatar" role="img" aria-label="Customer profile picture"></div>
    <p class="review-quote">I've used a few different services for this and Pelmora is by far the best. Fraction of the cost and I have the required docs within a couple of hours at most. Makes my life so much easier.</p>
    <p class="review-author">Marcus Tellby, NLG Calgary</p>
  </section>

  <section class="band">Compare KEX Services</section>

  <section class="compare">
    <div class="compare-brand"><span class="brand-mark"></span>Pelmora</div>
    <div class="compare-rival">‘Other Guys’</div>
    <table class="compare-table">
      <tr><td class="label"><svg width="14" height="14" viewBox="0 0 14 14"><circle cx="7" cy="7" r="5.5" fill="none" stroke="#fff" stroke-width="1.6"/><path d="M4.3 7.2l2 2 4.5-5" fill="none" stroke="#fff" stroke-width="1.8"/></svg>Price</td><td class="ours">$29 / month</td><td class="theirs">$39 / Order</td></tr>
      <tr><td class="label"><svg width="14" height="14" viewBox="0 0 14 14"><circle cx="7" cy="7" r="5.5" fill="none" stroke="#fff" stroke-width="1.6"/><path d="M4.3 7.2l2 2 4.5-5" fill="none" stroke="#fff" stroke-width="1.8"/></svg>Units</td><td class="ours">Unlimited</td><td class="theirs">Just One</td></tr>
      <tr><td class="label"><svg width="14" height="14" viewBox="0 0 14 14"><circle cx="7" cy="7" r="5.5" fill="none" stroke="#fff" stroke-width="1.6"/><path d="M4.3 7.2l2 2 4.5-5" fill="none" stroke="#fff" stroke-width="1.8"/></svg>Turnaround</td><td class="ours">4 Hours</td><td class="theirs">1 Day</td></tr>
      <tr><td class="label"><svg width="14" height="14" viewBox="0 0 14 14"><circle cx="7" cy="7" r="5.5" fill="none" stroke="#fff" stroke-width="1.6"/><path d="M4.3 7.2l2 2 4.5-5" fill="none" stroke="#fff" stroke-width="1.8"/></svg>Other Services</td><td class="ours">Several</td><td class="theirs">X</td></tr>
    </table>
  </section>

  <section class="cta-area">
    <div class="cta-button">
      <span class="cta-main">GET STARTED NOW</span>
      <span class="cta-sub">30-Day Money Back Guarantee</span>
    </div>
  </section>

  <section class="about">
    <div class="about-visual" role="img" aria-label="Photo of blue office file binders on a shelf">
      <div class="about-visual-name">Pelmora</div>
    </div>
    <div class="about-content">
      <div class="band">About Us</div>
      <p class="about-text">Pelmora provides on-demand administrative support for Mortgage Professionals across Canada. Everything from Notice of Assessment and Title Orders to inbound document sorting and lender fulfilment can be outsouced at a fraction of the cost of a full time administrator.</p>
    </div>
  </section>

  <footer class="footer">
    <span class="footer-copy">© Pelmora 2016 All rights reserved.</span>
    <span class="footer-unsub">Unsubscribe here</span>
  </footer>
</main>
</body>
</html>
```